Business Cards - Brightpath Horizon

need to design unique business card for my mortgage business. I need to design credit card style business card for my business or any unique idea that you might have

Target Market(s)

Home Loan customers

Industry/Entity Type

Mortgage Brokerage

Contact Information for Business Card

please design credit card style or very unique style business card

Colors

Designer to choose colors to be used in the design.

Requirements
Must have
• Name
• position
• Phone number
• fax number
• email address
• website address
• social media address
• All above fields will be provided once design in finalised

```html
<!DOCTYPE html>
<html lang="en">
<head>
<meta charset="utf-8">
<title>Brightpath Horizon – Business Card</title>
<link href="https://fonts.googleapis.com/css2?family=Playfair+Display:wght@400&family=Roboto:wght@400;500;700&display=swap" rel="stylesheet">
<style>
  :root {
    --backdrop: #2b2b2b;
    --paper: #f2f2f2;
    --brand-blue: #0a2fc4;
    --sky-blue: #1ea6f0;
    --brand-orange: #ff8c14;
    --white: #ffffff;
  }
  * { margin: 0; padding: 0; box-sizing: border-box; }
  html, body { width: 1200px; height: 960px; overflow: hidden; }
  body {
    background: var(--backdrop);
    position: relative;
    font-family: "Roboto", Arial, sans-serif;
  }
  .card {
    position: absolute;
    width: 600px;
    height: 342px;
    overflow: hidden;
  }
  /* Front */
  .card-front { left: 314px; top: 113px; background: var(--paper); }
  .brand-lockup {
    position: absolute;
    left: 0; right: 0; top: 72px;
    text-align: center;
  }
  .brand-name {
    font-family: "Playfair Display", Georgia, serif;
    font-weight: 400;
    font-size: 36px;
    line-height: 40px;
    letter-spacing: 1px;
    text-transform: uppercase;
  }
  .card-front .brand-name { color: var(--brand-blue); }
  .divider-blue {
    position: absolute; left: 0; top: 213px;
    width: 600px; height: 4px; background: var(--brand-blue);
  }
  .divider-orange {
    position: absolute; right: 0; top: 214px;
    width: 180px; height: 3px; background: var(--brand-orange);
  }
  .info-band {
    position: absolute; left: 0; top: 220px;
    width: 600px; height: 122px; background: var(--brand-blue);
    color: var(--white);
  }
  .contact-list { position: absolute; left: 26px; top: 29px; list-style: none; }
  .contact-list li {
    display: flex; align-items: center;
    height: 19px; font-size: 14px;
  }
  .contact-list svg { width: 14px; height: 14px; margin-right: 10px; fill: var(--sky-blue); }
  .person { position: absolute; right: 31px; top: 24px; text-align: right; }
  .person-name { font-size: 20px; font-weight: 500; color: var(--sky-blue); line-height: 24px; }
  .person-role { font-size: 15px; font-weight: 500; line-height: 22px; }
  .person-address { font-size: 14px; line-height: 19px; margin-top: 1px; }
  /* Back */
  .card-back { left: 311px; top: 472px; background: var(--brand-orange); }
  .card-back .brand-lockup { top: 131px; }
  .card-back .brand-name { color: var(--white); }
  .social-row {
    position: absolute; left: 0; top: 290px; width: 600px; height: 28px;
  }
  .social-rule {
    position: absolute; top: 13px; height: 2px; width: 155px;
  }
  .social-rule.left { left: 70px; background: linear-gradient(to right, rgba(255,255,255,0), var(--white)); }
  .social-rule.right { left: 375px; background: linear-gradient(to left, rgba(255,255,255,0), var(--white)); }
  .social-dot {
    position: absolute; top: 0; width: 28px; height: 28px;
    border-radius: 50%; background: var(--white);
  }
</style>
</head>
<body>

<section class="card card-front">
  <div class="brand-lockup">
    <div class="brand-name">Brightpath<br>Horizon</div>
  </div>
  <div class="divider-blue"></div>
  <div class="divider-orange"></div>
  <div class="info-band">
    <ul class="contact-list">
      <li><svg viewBox="0 0 16 16"><path d="M3.5 1l2.5 3-1.5 1.8c.9 2 2.3 3.4 4.2 4.2L10.5 8.5l3 2.5-1.4 2.8C6.8 13.4 2.6 9.2 1 3.9z"/></svg>907 214 3865</li>
      <li><svg viewBox="0 0 16 16"><rect x="4" y="1" width="8" height="4"/><rect x="1" y="6" width="14" height="6" rx="1"/><rect x="4" y="10" width="8" height="5" fill="#fff"/></svg>907 214 3866</li>
      <li><svg viewBox="0 0 16 16"><path d="M1 3h14v10H1z M1 3l7 6 7-6" fill="none" stroke="#1ea6f0" stroke-width="1.6"/></svg>daniel@brightpath.com</li>
      <li><svg viewBox="0 0 16 16"><circle cx="8" cy="8" r="6.5" fill="none" stroke="#1ea6f0" stroke-width="1.6"/><path d="M1.5 8h13M8 1.5c-3 3.5-3 9.5 0 13M8 1.5c3 3.5 3 9.5 0 13" fill="none" stroke="#1ea6f0" stroke-width="1.2"/></svg>www.brightpath.com</li>
    </ul>
    <div class="person">
      <div class="person-name">DANIEL REYES</div>
      <div class="person-role">CEO/FOUNDER</div>
      <div class="person-address">2143 Willow Crest Road<br>Juneau, Alaska 99801</div>
    </div>
  </div>
</section>

<section class="card card-back">
  <div class="brand-lockup">
    <div class="brand-name">Brightpath<br>Horizon</div>
  </div>
  <div class="social-row" aria-label="Social media links">
    <div class="social-rule left"></div>
    <span class="social-dot" style="left:237px"></span>
    <span class="social-dot" style="left:269px"></span>
    <span class="social-dot" style="left:302px"></span>
    <span class="social-dot" style="left:335px"></span>
    <div class="social-rule right"></div>
  </div>
</section>

</body>
</html>
```